Business Card Design - Photographer

I am a landscape photographer and I require a business card design. 

I require two designs:
1)  a double sided business card
 and
b)  a single sided business card 

The single sided design can either be the same as the double sided (with just one side having all the information)....or it can be an entire new design. Its up to you.

My corporate colours are (CMYK):

Blue   69, 32, 0, 0
Grey  72,  64,  47,  31
Green  32,  2,  91,  0
Yellow   0, 19, 92, 0
Orange  0, 39, 75, 0

Colour space in final file should be in CMYK.

The details that need to be included on the card:

- Use the provided Logo
- Name: Wiktor Baranowski
- Email:   sales@vistalumeworks.com.au
- Website:    vistalumeworks.com.au
- Twitter:    twitter.com/vistalumeworks
- Facebook:   facebook.com/vistalumeworks
- Mobile  0417 539 662

Please use the attached template to design the logo to the specified size, including the marked bleed lines. I have also attached my logo in PNG (transparent background) and ai format for you to use.

The final file should be:
- Photoshop version with layers so I can edit the name/text etc. All non vector files should be high resolution at 1039 x 697 pixels at 300 dpi.

I also require a file as:
- Vector based PDF

Anyway questions please contact me.

Thank you

Industry/Entity Type

Landscape

Logo styles of interest
Pictorial/Combination Logo
Abstract Logo
Wordmark Logo
Lettermark Logo
Requirements
Must have
• The details that need to be included on the card:

- Use the provided Logo
- Name: Wiktor Baranowski
- Email: sales@vistalumeworks.com.au
- Website: vistalumeworks.com.au
- Twitter: twitter.com/vistalumeworks
- Facebook: facebook.com/vistalumeworks
- Mobile 0417 539 662

```html
<!DOCTYPE html>
<html lang="en">
<head>
<meta charset="utf-8">
<title>Vistalume Works – Business Cards</title>
<link href="https://fonts.googleapis.com/css2?family=Cinzel:wght@500&family=Arimo:wght@400;700&display=swap" rel="stylesheet">
<style>
  :root {
    --stage: #a8862a;
    --card-light: #ffffff;
    --card-dark-center: #4a4f60;
    --card-dark-edge: #0c0e16;
    --ink: #3c4150;
    --ink-soft: #2a2d36;
    --accent-blue: #2e8fd4;
    --on-dark: #ffffff;
    --tab: #3c4150;
  }
  * { margin: 0; padding: 0; box-sizing: border-box; }
  html, body { width: 1200px; height: 686px; overflow: hidden; }
  body { background: var(--stage); position: relative; font-family: "Arimo", Arial, sans-serif; }

  .card {
    position: absolute;
    width: 482px; height: 276px;
    border-radius: 26px;
    background: var(--card-light);
    box-shadow: 0 2px 3px rgba(0,0,0,.35);
    overflow: hidden;
    color: var(--ink);
  }
  .card--contact { left: 64px; top: 50px; }
  .card--brand  { left: 668px; top: 53px; }
  .card--dark {
    left: 358px; top: 361px;
    background: radial-gradient(ellipse at 50% 40%, var(--card-dark-center) 0%, #23262f 55%, var(--card-dark-edge) 100%);
    color: var(--on-dark);
  }

  .card__tab { position: absolute; top: 83px; width: 7px; height: 112px; background: var(--tab); }
  .card__tab--left { left: 0; border-radius: 0 5px 5px 0; }
  .card__tab--right { right: 0; border-radius: 5px 0 0 5px; }
  .card--dark .card__tab { background: var(--on-dark); }

  .brand-mark {
    position: absolute; left: 50%;
    width: 80px; height: 80px; margin-left: -40px;
    border-radius: 50%; background: var(--ink);
  }
  .card--dark .brand-mark { background: var(--on-dark); }

  .brand-name {
    position: absolute; left: 0; width: 100%;
    text-align: center;
    font-family: "Cinzel", "Times New Roman", serif;
    font-weight: 500; font-size: 19px; letter-spacing: 0;
    text-transform: uppercase;
    line-height: 1;
  }
  .brand-rule {
    position: absolute; left: 50%;
    width: 220px; margin-left: -110px; height: 1px;
    background: currentColor;
  }
  .brand-tagline {
    position: absolute; left: 0; width: 100%;
    text-align: center;
    font-family: "Cinzel", "Times New Roman", serif;
    font-size: 8.5px; letter-spacing: 1.4px; line-height: 1;
    text-transform: uppercase;
  }
  .divider {
    position: absolute; left: 50%; top: 166px;
    width: 130px; margin-left: -65px; height: 1px;
    background: linear-gradient(90deg, transparent, var(--ink-soft), transparent);
  }

  .contact { position: absolute; left: 0; top: 0; width: 100%; color: var(--ink-soft); line-height: 1; }
  .contact__row {
    position: absolute; left: 0; width: 100%;
    text-align: center; font-size: 12px; white-space: nowrap;
  }
  .contact__item { display: inline-flex; align-items: center; gap: 4px; margin: 0 6px; vertical-align: middle; }
  .contact__item svg { display: block; }
  .social-square { width: 13px; height: 13px; background: var(--ink); display: inline-block; }
  .contact__name { font-size: 12.5px; font-weight: 700; letter-spacing: .3px; color: var(--ink); }
  .contact__address { font-size: 12.5px; }
  .contact__web { font-size: 13px; font-weight: 700; }
  .contact__web .highlight { color: var(--accent-blue); }
</style>
</head>
<body>

  <!-- Double-sided card: information side -->
  <section class="card card--contact">
    <span class="card__tab card__tab--left"></span>
    <span class="card__tab card__tab--right"></span>
    <span class="brand-mark" style="top:26px;"></span>
    <div class="brand-name" style="top:120px;">Vistalume Works</div>
    <span class="brand-rule" style="top:141px;"></span>
    <div class="brand-tagline" style="top:148px;">Fine Art Photography</div>
    <span class="divider"></span>

    <div class="contact">
      <div class="contact__row contact__name" style="top:173px;">Wiktor Baranowski</div>
      <div class="contact__row" style="top:191px;">
        <span class="contact__item">
          <svg width="9" height="12" viewBox="0 0 9 12"><path d="M2 0.5 L4 3 L2.8 4.5 Q3.5 7 5.5 8.6 L7 7.6 L9 10 L7.4 11.5 Q1.5 10 0.3 2 Z" fill="#2e8fd4"/></svg>
          0417 539 662
        </span>
        <span class="contact__item">
          <svg width="13" height="9" viewBox="0 0 13 9"><rect width="13" height="9" fill="#2e8fd4"/><path d="M0 0 L6.5 5 L13 0" fill="none" stroke="#fff" stroke-width="1.2"/></svg>
          sales@vistalumeworks.com.au
        </span>
      </div>
      <div class="contact__row" style="top:208px;">
        <span class="contact__item"><span class="social-square"></span>@vistalumeworks</span>
        <span class="contact__item"><span class="social-square"></span>@vistalumeworks</span>
      </div>
      <div class="contact__row contact__address" style="top:226px;">Street name City, State, zip code</div>
      <div class="contact__row contact__web" style="top:244px;">www.<span class="highlight">vistalumeworks</span>.com.au</div>
    </div>
  </section>

  <!-- Double-sided card: brand side -->
  <section class="card card--brand">
    <span class="card__tab card__tab--left"></span>
    <span class="card__tab card__tab--right"></span>
    <span class="brand-mark" style="top:66px;"></span>
    <div class="brand-name" style="top:167px;">Vistalume Works</div>
    <span class="brand-rule" style="top:188px;"></span>
    <div class="brand-tagline" style="top:195px;">Fine Art Photography</div>
  </section>

  <!-- Single-sided card: dark version -->
  <section class="card card--dark">
    <span class="card__tab card__tab--left"></span>
    <span class="card__tab card__tab--right"></span>
    <span class="brand-mark" style="top:63px;"></span>
    <div class="brand-name" style="top:174px;">Vistalume Works</div>
    <span class="brand-rule" style="top:196px;"></span>
    <div class="brand-tagline" style="top:203px;">Fine Art Photography</div>
  </section>

</body>
</html>
```